Schlichtes Design für Malerbetrieb
Zielgruppe
Wir sind ein mittelgroßer Malerbetrieb in München mit umfangreichem Leistungsspektrum.
Unsere Hauptleistungen sind: Fassadenrenovierung, Altbausanierung, Betoninstandsetzung, Balkonabdichtung (kein Neubau!).
Unsere Zielgruppen sind: Hausverwaltungen, Firmen und Privatpersonen.
Unsere Kunden schätzen: Konstruktive Organisation und Planung im Vorfeld, Zuverlässigkeit, saubere Arbeitsweise, dauerhafte Balkonabdichtungen.
Aufgabenstellung
Wir möchten eine langlebige, stilvolle, minimalistische Homepage.
Wir möchten von der bestehenden Homepage nur die Schriftart für unseren Firmennamen (Century Gothic) und wenn möglich (nicht zwingend), irgendwo das florale Muster einbauen. Corporate-Design haben wir nicht.
Farbtöne: Firmennamen Orange (hellorange bis erdiges Orange möglich, da sind wir nicht fixiert) , einen dunklen Hintergrundfarbton (Petrol-Blaugrau ?) mit gelbem (neon bis senfgelb) Akzent (Linien), Blumenmuster weiß, grau.
Dies sind nur unsere Ideen. Wir sind aber auch absolut offen für eure Profi-Ideen.
Wir möchten uns von den unzähligen langweiligen 'Pinselseiten mit veralteten Bilder' unserer Kollegen interessant und mit Stil abheben.
Eher nach dem Motto 'weniger ist mehr'.
Einen positiven, sympathischen Eindruck geben und unsere Leistungen in den Vordergrund bringen.
Da wir viele Stammkunden haben, betreiben wir kein Social-Media und möchten dies vorerst auch nicht tun.
Die Seite wird in den nächsten Jahren nicht verändert, höchstens die Bilder aktualisiert.
Die Texte haben wir alle selbst entworfen und möchten wir so übernehmen.
Die Galerien sollen unkompliziert anzuschauen sein.
Uns gefällt die Struktur und Schlichtheit von https://vaartmolen.nl/ oder Timbra.de gut und wir mögen Vintage-Grafiken gerne.
Einerseits darf die Seite geradlinig, andererseits aber auch rund und floral wirken.

```html
<!DOCTYPE html>
<html lang="de">
<head>
<meta charset="utf-8">
<title>kolbrit – Malerarbeiten</title>
<link href="https://fonts.googleapis.com/css2?family=Fira+Sans+Condensed:wght@400&display=swap" rel="stylesheet">
<style>
  :root {
    --charcoal: #3b3a3c;
    --damask-grey: #5d5c5f;
    --blue: #0f70b4;
    --yellow: #f6e61e;
    --rose: #d8a4a1;
    --white: #ffffff;
  }
  html, body {
    margin: 0;
    padding: 0;
    width: 1200px;
    height: 900px;
    overflow: hidden;
    background: var(--charcoal);
  }
  .page {
    position: relative;
    width: 1200px;
    height: 900px;
    background: var(--charcoal);
    font-family: "Fira Sans Condensed", "Arial Narrow", sans-serif;
    font-weight: 400;
  }
  .hero-graphic {
    position: absolute;
    inset: 0;
    width: 1200px;
    height: 900px;
  }
  .site-header {
    position: absolute;
    top: 0;
    left: 0;
    width: 1200px;
    height: 126px;
  }
  .brand-small {
    position: absolute;
    top: 18px;
    right: 42px;
    margin: 0;
    font-size: 48px;
    line-height: 1;
    color: var(--yellow);
  }
  .main-nav {
    position: absolute;
    top: 88px;
    left: 56px;
    right: 46px;
    display: flex;
    justify-content: space-between;
    margin: 0;
    padding: 0;
    list-style: none;
  }
  .main-nav a {
    color: var(--white);
    text-decoration: none;
    font-size: 24px;
    line-height: 1;
  }
  .hero-title {
    position: absolute;
    left: 130px;
    top: 400px;
    width: 440px;
    margin: 0;
    text-align: center;
    font-weight: 400;
    color: var(--charcoal);
  }
  .hero-title .name {
    display: block;
    font-size: 104px;
    line-height: 1;
  }
  .hero-subtitle {
    position: absolute;
    left: 130px;
    top: 512px;
    width: 440px;
    margin: 0;
    text-align: center;
    font-size: 28px;
    line-height: 1;
    color: var(--white);
  }
  .site-footer {
    position: absolute;
    left: 0;
    bottom: 0;
    width: 1200px;
    height: 59px;
  }
  .footer-nav {
    position: absolute;
    right: 14px;
    top: 15px;
    display: flex;
    gap: 24px;
    margin: 0;
    padding: 0;
    list-style: none;
  }
  .footer-nav a {
    color: var(--white);
    text-decoration: none;
    font-size: 25px;
    line-height: 1;
  }
</style>
</head>
<body>
<div class="page">
  <svg class="hero-graphic" viewBox="0 0 1024 768" preserveAspectRatio="none">
    <rect class="damask-area" x="0" y="108" width="1024" height="610" fill="var(--damask-grey)" role="img" aria-label="Florales Damastmuster in Grau auf dunklem Grund"/>
    <polygon class="shape-blue" points="0,108 225,108 740,355 518,465 0,712" fill="var(--blue)"/>
    <polygon class="shape-yellow" points="1024,215 1024,688 518,465" fill="var(--yellow)"/>
    <polygon class="shape-rose" points="235,600 518,465 1024,688 1024,718 355,718" fill="var(--rose)"/>
  </svg>

  <header class="site-header">
    <p class="brand-small">kolbrit</p>
    <ul class="main-nav">
      <li><a href="#">malerarbeiten</a></li>
      <li><a href="#">betoninstandsetzung</a></li>
      <li><a href="#">balkonabdichtung</a></li>
      <li><a href="#">farbgestaltung</a></li>
      <li><a href="#">wärmedämmung</a></li>
      <li><a href="#">ausbildung</a></li>
      <li><a href="#">portrait</a></li>
    </ul>
  </header>

  <h1 class="hero-title"><span class="name">kolbrit</span></h1>
  <p class="hero-subtitle">Malerarbeiten</p>

  <footer class="site-footer">
    <ul class="footer-nav">
      <li><a href="#">Kontakt</a></li>
      <li><a href="#">Impressum</a></li>
      <li><a href="#">Datenschutz</a></li>
    </ul>
  </footer>
</div>
</body>
</html>
```